wealth management firm, professional group, new model

we have a logo that works but we need a card, white background using our colors...clean look

our tag line if can be used in

Guiding Clients Toward Lasting Ownership

```html
<!DOCTYPE html>
<html lang="en">
<head>
<meta charset="utf-8">
<title>Arvel Wealth Partners – Business Card</title>
<link href="https://fonts.googleapis.com/css2?family=Lato:wght@400;700&display=swap" rel="stylesheet">
<style>
  :root {
    --navy: #1c2f55;
    --navy-deep: #162746;
    --paper: #ffffff;
    --backdrop-top: #8fa9c6;
    --backdrop-bottom: #6f86ab;
    --shadow: rgba(20, 35, 65, 0.28);
  }
  * { box-sizing: border-box; margin: 0; padding: 0; }
  html, body { width: 1200px; height: 876px; overflow: hidden; }
  body {
    background: linear-gradient(160deg, var(--backdrop-top), var(--backdrop-bottom));
    font-family: "Lato", sans-serif;
    position: relative;
  }
  .card {
    position: absolute;
    width: 520px;
    height: 298px;
    background: var(--paper);
    box-shadow: 0 14px 30px var(--shadow);
    overflow: hidden;
  }
  .card--front { left: 50px; top: 460px; }
  .card--back { left: 630px; top: 118px; }

  /* Company name: one font, one weight, one colour, plain circle beside */
  .brand-name {
    position: absolute;
    left: 0; right: 0;
    display: flex;
    align-items: center;
    justify-content: center;
    gap: 12px;
    font-family: "Lato", sans-serif;
    font-weight: 400;
    font-size: 30px;
    line-height: 1;
    white-space: nowrap;
  }
  .brand-name__dot {
    width: 14px;
    height: 14px;
    border-radius: 50%;
    background: currentColor;
    flex: none;
  }

  /* Front */
  .front__panel {
    position: absolute;
    left: 0; top: 0;
    width: 100%;
    height: 204px;
    background: linear-gradient(120deg, #2a4270 0%, var(--navy) 45%, var(--navy-deep) 100%);
  }
  .front__frame { position: absolute; inset: 0; }
  .front__panel .brand-name {
    top: 88px;
    color: var(--paper);
  }
  .front__contacts {
    position: absolute;
    left: 30px;
    top: 216px;
    list-style: none;
    color: var(--navy);
    font-size: 12px;
    line-height: 20px;
  }
  .front__contacts li { display: flex; align-items: center; gap: 6px; }
  .front__contacts svg { width: 11px; height: 11px; flex: none; }
  .front__person {
    position: absolute;
    right: 32px;
    top: 232px;
    text-align: right;
    color: var(--navy);
  }
  .person__name {
    font-weight: 700;
    font-size: 17px;
    letter-spacing: 0.02em;
  }
  .person__role { font-size: 13px; margin-top: 2px; }

  /* Back */
  .card--back .brand-name {
    top: 112px;
    color: var(--navy);
  }
  .back__tagline {
    position: absolute;
    left: 0; right: 0;
    top: 178px;
    text-align: center;
    font-family: "Lato", sans-serif;
    font-weight: 400;
    font-size: 14px;
    letter-spacing: 0.04em;
    color: var(--navy);
  }
</style>
</head>
<body>

<section class="card card--front" aria-label="Card front">
  <div class="front__panel">
    <p class="brand-name"><span class="brand-name__dot" aria-hidden="true"></span>Arvel Wealth Partners</p>
  </div>

  <svg class="front__frame" viewBox="0 0 520 298" aria-hidden="true">
    <defs>
      <clipPath id="clip-panel"><rect x="0" y="0" width="520" height="204"/></clipPath>
      <clipPath id="clip-strip"><rect x="0" y="204" width="520" height="94"/></clipPath>
    </defs>
    <rect x="16" y="16" width="488" height="266" fill="none" stroke="#ffffff" stroke-width="1.5" clip-path="url(#clip-panel)"/>
    <rect x="16" y="16" width="488" height="266" fill="none" stroke="#1c2f55" stroke-width="1.5" clip-path="url(#clip-strip)"/>
  </svg>

  <ul class="front__contacts">
    <li>
      <svg viewBox="0 0 12 12"><circle cx="6" cy="6" r="6" fill="#1c2f55"/><rect x="3" y="4" width="6" height="4" fill="none" stroke="#fff" stroke-width="0.9"/><path d="M3 4 L6 6.3 L9 4" fill="none" stroke="#fff" stroke-width="0.9"/></svg>
      hello@arvelwealth.co
    </li>
    <li>
      <svg viewBox="0 0 12 12"><circle cx="6" cy="6" r="6" fill="#1c2f55"/><path d="M4.2 3.2 L5.3 4.6 L4.7 5.4 Q5.6 7 6.8 7.4 L7.5 6.8 L8.8 7.8 L8.2 8.8 Q5.5 8.8 3.4 4.2 Z" fill="#fff"/></svg>
      021 555 0147
    </li>
    <li>
      <svg viewBox="0 0 12 12"><circle cx="6" cy="6" r="6" fill="#1c2f55"/><circle cx="6" cy="6" r="3.4" fill="none" stroke="#fff" stroke-width="0.8"/><ellipse cx="6" cy="6" rx="1.4" ry="3.4" fill="none" stroke="#fff" stroke-width="0.8"/><line x1="2.6" y1="6" x2="9.4" y2="6" stroke="#fff" stroke-width="0.8"/></svg>
      www.arvelwealth.com
    </li>
  </ul>

  <div class="front__person">
    <p class="person__name">DANIEL REYES</p>
    <p class="person__role">Director</p>
  </div>
</section>

<section class="card card--back" aria-label="Card back">
  <p class="brand-name"><span class="brand-name__dot" aria-hidden="true"></span>Arvel Wealth Partners</p>
  <p class="back__tagline">Guiding Clients Toward Lasting Ownership</p>
</section>

</body>
</html>
```